Local Roofing/Construction company business needs new biz card design

We need a new business card design, current cards are from the start of this operation and generic at best. We are a local Construction Company (General Contractor) with a majority of our work originating from insurance claims-exterior finish work is the main focus (Roofs-Siding-Gutters etc). Heavily involved with homeowners and the low ball offers they receive from insurance company's after a insurable event takes place. I have attached some of our original logo file(s) below.

```html
<!DOCTYPE html>
<html lang="en">
<head>
<meta charset="utf-8">
<title>Tallgrass Builders – Business Card</title>
<link rel="stylesheet" href="https://fonts.googleapis.com/css2?family=Montserrat:wght@800&family=Open+Sans:wght@400;600;700&display=swap">
<style>
  :root{
    --stage:#232323;
    --green:#4cba6b;
    --green-deep:#3fa85d;
    --night:#061c20;
    --night-2:#0a2428;
    --night-3:#0d2a2f;
    --white:#ffffff;
  }
  *{box-sizing:border-box;margin:0;padding:0}
  html,body{width:1200px;height:780px;overflow:hidden;background:var(--stage)}
  .canvas{position:relative;width:1200px;height:780px;font-family:"Open Sans",sans-serif}
  .card{position:absolute;top:128px;width:300px;height:525px;border-radius:18px;overflow:hidden;box-shadow:0 14px 30px rgba(0,0,0,.55)}

  /* back */
  .card--back{left:230px;background:var(--green)}
  .back-pattern{position:absolute;inset:0;background:linear-gradient(160deg,var(--green) 0%,var(--green-deep) 100%)}
  .back-mark{position:absolute;top:26px;right:24px;display:flex;align-items:center;gap:6px;color:var(--white);font-weight:700;font-size:11px;letter-spacing:.06em}
  .back-mark__square{width:12px;height:12px;background:var(--white);border-radius:2px}

  /* front */
  .card--front{left:670px;background:var(--night)}
  .front-curves{position:absolute;inset:0}
  .brand-band{position:absolute;top:40px;left:35px;width:230px;height:56px;background:var(--green);
    clip-path:polygon(14px 0,calc(100% - 14px) 0,100% 14px,100% calc(100% - 14px),calc(100% - 14px) 100%,14px 100%,0 calc(100% - 14px),0 14px);
    display:flex;align-items:center;justify-content:center}
  .brand-band__name{font-family:"Open Sans",sans-serif;font-weight:700;font-size:19px;letter-spacing:.05em;color:var(--night)}
  .person{position:absolute;top:178px;left:0;right:0;text-align:center}
  .person__name{font-family:"Montserrat",sans-serif;font-weight:800;font-size:25px;line-height:1.1}
  .person__first{color:var(--green)}
  .person__last{color:var(--white)}
  .person__role{color:var(--white);font-size:13px;font-weight:600;margin-top:4px}
  .icon-row{position:absolute;top:246px;left:0;right:0;display:flex;justify-content:center;gap:9px}
  .icon{width:24px;height:24px;border-radius:50%;background:var(--green);display:flex;align-items:center;justify-content:center}
  .icon svg{width:14px;height:14px}
  .contact{position:absolute;top:282px;left:0;right:0;text-align:center;color:var(--white);font-size:13px;line-height:19px}
  .address{position:absolute;top:418px;left:0;right:0;text-align:center;color:var(--white);font-size:13px;line-height:19px}
  .address .icon{margin:0 auto 8px}
</style>
</head>
<body>
<main class="canvas">

  <section class="card card--back" aria-label="Card back">
    <div class="back-pattern" role="img" aria-label="Repeating company monogram pattern in tonal greens"></div>
    <div class="back-mark"><span class="back-mark__square"></span>TALLGRASS</div>
  </section>

  <section class="card card--front" aria-label="Card front">
    <svg class="front-curves" viewBox="0 0 300 525" preserveAspectRatio="none" aria-hidden="true">
      <path d="M0 330 Q 150 420 300 250 L300 525 L0 525 Z" fill="var(--night-3)"/>
      <path d="M0 370 Q 170 400 300 310 L300 525 L0 525 Z" fill="var(--night-2)"/>
      <path d="M60 525 Q 200 420 300 360 L300 525 Z" fill="var(--night)"/>
    </svg>

    <div class="brand-band"><span class="brand-band__name">TALLGRASS BUILDERS</span></div>

    <div class="person">
      <h1 class="person__name"><span class="person__first">Dana</span> <span class="person__last">Whitfield</span></h1>
      <p class="person__role">Co-Founder</p>
    </div>

    <div class="icon-row">
      <span class="icon"><svg viewBox="0 0 24 24"><path fill="#fff" d="M6.6 10.8a15 15 0 0 0 6.6 6.6l2.2-2.2c.3-.3.7-.4 1-.2 1.1.4 2.3.6 3.6.6.6 0 1 .4 1 1V20c0 .6-.4 1-1 1A17 17 0 0 1 3 4c0-.6.4-1 1-1h3.5c.6 0 1 .4 1 1 0 1.3.2 2.5.6 3.6.1.3 0 .7-.2 1z"/></svg></span>
      <span class="icon"><svg viewBox="0 0 24 24"><rect x="3" y="6" width="18" height="12" rx="1.5" fill="#fff"/><path d="M3.5 6.5 12 13l8.5-6.5" stroke="var(--green)" stroke-width="1.6" fill="none"/></svg></span>
      <span class="icon"><svg viewBox="0 0 24 24" fill="none" stroke="#fff" stroke-width="1.8"><circle cx="12" cy="12" r="9"/><ellipse cx="12" cy="12" rx="4" ry="9"/><path d="M3 12h18"/></svg></span>
    </div>

    <div class="contact">
      <p>555-201-4410</p>
      <p>555-201-7730 (Emergency)</p>
      <p>www.tallgrassbuilders.com</p>
      <p>hello@tallgrassbuilders.com</p>
    </div>

    <div class="address">
      <span class="icon"><svg viewBox="0 0 24 24"><path fill="#fff" d="M12 2a7 7 0 0 0-7 7c0 5 7 13 7 13s7-8 7-13a7 7 0 0 0-7-7zm0 9.5A2.5 2.5 0 1 1 12 6.5a2.5 2.5 0 0 1 0 5z"/></svg></span>
      <p>48 Birch Hollow</p>
      <p>Dr, Fairview, MO 63012</p>
    </div>
  </section>

</main>
</body>
</html>
```